I need an amazing business card!

I am the principle in my own software company that develops zorPad and mobile applications. I require a great business card design. I've attached my corporate logo (Thanks Tomas!).
I would like the design to integrate the logo, my name, email address and skype account:
name Brent Olafsen
email brentolafsen@tavrik.com
skype brentolafsen.net
I would like the back of the card to have a "write on me area" similar to the "write on me" card on this page, row 6:
http://us.prindlewick.com/design-templates/business-cards/#industry=Computing%20%26%20IT
As far as the rest - it's all you!
Updates
1) Please add an example telephone number as well.
Industry/Entity Type
Software
Look and feel
Each slider illustrates characteristics of the customer's brand and the style your logo design should communicate.

```html
<!DOCTYPE html>
<html lang="en">
<head>
<meta charset="utf-8">
<title>Brent Olafsen — Business Card</title>
<link href="https://fonts.googleapis.com/css2?family=Jura:wght@500;600&family=Lato:wght@400&display=swap" rel="stylesheet">
<style>
  :root {
    --stage: #e7e4df;
    --card-black: #1a1a1a;
    --card-black-deep: #0c0c0c;
    --lime: #cfe38a;
    --lime-light: #e6f2b6;
    --lime-mid: #b7d45c;
    --lime-brand: #8fb83a;
    --ink: #111111;
  }
  html, body {
    margin: 0;
    width: 1200px;
    height: 1000px;
    overflow: hidden;
    background: var(--stage);
  }
  .canvas {
    position: relative;
    width: 1200px;
    height: 1000px;
  }
  .card {
    position: absolute;
    left: 276px;
    width: 648px;
    height: 392px;
    box-shadow: 0 8px 24px rgba(0,0,0,0.25);
    overflow: hidden;
  }
  .card-front { top: 80px; }
  .card-back { top: 528px; background: radial-gradient(ellipse at 45% 40%, #2a2a2a, var(--card-black-deep)); }
  .card-bg { position: absolute; left: 0; top: 0; }

  .brand-mark {
    position: absolute;
    left: 72px;
    top: 127px;
    width: 116px;
    height: 116px;
    border-radius: 24px;
    background: linear-gradient(160deg, var(--lime-mid), var(--lime-brand));
  }
  .brand-name {
    position: absolute;
    left: 40px;
    top: 250px;
    width: 180px;
    text-align: center;
    font-family: "Jura", sans-serif;
    font-weight: 600;
    font-size: 30px;
    letter-spacing: 12px;
    color: var(--lime-brand);
  }
  .holder-name {
    position: absolute;
    left: 304px;
    top: 120px;
    margin: 0;
    white-space: nowrap;
    font-family: "Jura", sans-serif;
    font-weight: 500;
    font-size: 40px;
    line-height: 48px;
    letter-spacing: 1.5px;
    color: var(--ink);
  }
  .contact-list {
    position: absolute;
    left: 310px;
    top: 186px;
    margin: 0;
    padding: 0;
    list-style: none;
    font-family: "Lato", sans-serif;
    font-size: 17px;
    color: var(--ink);
  }
  .contact-list li {
    display: flex;
    align-items: center;
    gap: 10px;
    height: 24px;
    margin-bottom: 12px;
    white-space: nowrap;
  }
  .contact-icon { display: block; width: 23px; height: 23px; flex: none; }

  .write-prompt {
    position: absolute;
    left: 58px;
    top: 48px;
    font-family: "Jura", sans-serif;
    font-weight: 500;
    font-size: 21px;
    color: var(--lime-mid);
  }
  .write-line {
    position: absolute;
    left: 48px;
    width: 580px;
    height: 42px;
    background: linear-gradient(90deg, var(--lime-mid), var(--lime-light) 50%, var(--lime));
    box-shadow: 0 0 8px rgba(200,230,120,0.55);
  }
  .faint-mark {
    position: absolute;
    left: 238px;
    top: 90px;
    width: 170px;
    height: 170px;
    border-radius: 36px;
    background: rgba(143,184,58,0.35);
  }
  .faint-name {
    position: absolute;
    left: 160px;
    top: 262px;
    width: 330px;
    text-align: center;
    font-family: "Jura", sans-serif;
    font-weight: 600;
    font-size: 44px;
    letter-spacing: 22px;
    color: rgba(143,184,58,0.4);
  }
</style>
</head>
<body>
<main class="canvas">

  <section class="card card-front" aria-label="Card front">
    <svg class="card-bg" width="648" height="392" viewBox="0 0 648 392" aria-hidden="true">
      <defs>
        <radialGradient id="front-lime" cx="70%" cy="40%" r="70%">
          <stop offset="0" stop-color="#eef6c8"/>
          <stop offset="1" stop-color="#c5dc72"/>
        </radialGradient>
        <linearGradient id="front-dark" x1="0" y1="0" x2="1" y2="1">
          <stop offset="0" stop-color="#1f1f1f"/>
          <stop offset="1" stop-color="#0c0c0c"/>
        </linearGradient>
      </defs>
      <rect width="648" height="392" fill="url(#front-lime)"/>
      <path d="M0 0 H240 C275 60 280 120 255 190 C230 260 225 330 245 392 H0 Z" fill="url(#front-dark)"/>
    </svg>
    <div class="brand-mark"></div>
    <div class="brand-name">tavrik</div>

    <h1 class="holder-name">Brent Olafsen</h1>
    <ul class="contact-list">
      <li>
        <svg class="contact-icon" viewBox="0 0 24 24" aria-hidden="true"><circle cx="12" cy="12" r="12" fill="#111"/><rect x="6" y="8" width="12" height="8.5" fill="none" stroke="#fff" stroke-width="1.5"/><path d="M6 8 L12 13 L18 8" fill="none" stroke="#fff" stroke-width="1.5"/></svg>
        <span>brentolafsen@tavrik.com</span>
      </li>
      <li>
        <svg class="contact-icon" viewBox="0 0 24 24" aria-hidden="true"><circle cx="12" cy="12" r="12" fill="#111"/><circle cx="12" cy="12" r="6" fill="none" stroke="#fff" stroke-width="1.6"/></svg>
        <span>brentolafsen.net</span>
      </li>
      <li>
        <svg class="contact-icon" viewBox="0 0 24 24" aria-hidden="true"><circle cx="12" cy="12" r="12" fill="#111"/><path d="M6 10 C6 7 18 7 18 10 L16 11 L15 9.5 H9 L8 11 Z" fill="#fff"/><rect x="7.5" y="12" width="9" height="5" rx="1" fill="#fff"/></svg>
        <span>(555) 404-7781</span>
      </li>
    </ul>
  </section>

  <section class="card card-back" aria-label="Card back">
    <div class="faint-mark"></div>
    <div class="faint-name">tavrik</div>
    <div class="write-prompt">You can write one me</div>
    <div class="write-line" style="top:86px"></div>
    <div class="write-line" style="top:156px"></div>
    <div class="write-line" style="top:226px"></div>
    <div class="write-line" style="top:296px"></div>
  </section>

</main>
</body>
</html>
```